Elegant, High End Integrated Wellness Healthcare Practice

We need a brochure designed for an integrated mind-body wellness healthcare practice (www.quellarivecare.com) . This brochure will be used when we cold call prospects (physicians to refer to our office, and potential consumers to utilize our services). Our practice is geographically located in the middle Tennessee USA region, although we have plans to become an international company as many of our offerings can be accessed anywhere in the world. Ultimately our goal is to have this brochure used as a leave-behind in an effort to introduce our integrated offerings to increase market share. The final product brochure should be both elegant and serious, with clean lines but also convey warmth and trust, as individuals who are coming for our services have usually struggled with their health for a significant amount of time before finding our practice.
Updates

The design brief was very specific about providing a high-end science-based 2-page brochure (not flier). Several designs submitted were fliers. The other designs were heavy on yoga or "woo woo" non-science-based looking pictures. This is a flier to appeal to physicians and other healthcare providers. Therefore the design must speak science and evidence-based methods of mind and body wellness care. I would also like to appeal to the other designers I paid extra for their submissions and who have indicated they will "respond in the coming days."

```html
<!DOCTYPE html>
<html lang="en">
<head>
<meta charset="utf-8">
<title>Quellarive Care – Brochure</title>
<link rel="stylesheet" href="https://fonts.googleapis.com/css2?family=Tinos:wght@400;700&display=swap">
<style>
  :root{
    --canvas:#e8e8e8;
    --navy:#0e1a3d;
    --navy-deep:#0b1533;
    --slate:#3c4a52;
    --green:#6fa83a;
    --green-dark:#243a0a;
    --ink:#1d2a10;
    --body:#333;
    --white:#ffffff;
  }
  *{margin:0;padding:0;box-sizing:border-box}
  html,body{width:1200px;height:768px;overflow:hidden;background:var(--canvas)}
  body{font-family:"Tinos","Times New Roman",serif;position:relative}

  .page{position:absolute;top:24px;width:556px;height:719px;overflow:hidden}
  .page--cover{left:24px;background:linear-gradient(180deg,var(--navy-deep) 0%,var(--navy) 22%,var(--slate) 48%,#6d7366 70%,#4a5256 100%)}
  .page--values{left:616px;background:var(--white)}

  /* brand lockup */
  .brand{position:absolute;display:flex;align-items:center}
  .brand__dot{border-radius:50%;flex:none}
  .brand__name{font-variant:small-caps;font-weight:400;line-height:1.05}
  .page--cover .brand{left:137px;top:23px;gap:10px}
  .page--cover .brand__dot{width:83px;height:83px;border:7px solid var(--white)}
  .page--cover .brand__name{color:var(--white);font-size:33px;text-align:center;width:190px}
  .page--values .brand{left:18px;top:13px;gap:8px}
  .page--values .brand__dot{width:58px;height:58px;border:5px solid var(--green)}
  .page--values .brand__name{color:var(--green-dark);font-size:23px;text-align:center;width:140px}

  .cover-photo{position:absolute;left:0;top:150px;width:556px;height:460px;
    background:radial-gradient(ellipse 55% 60% at 50% 45%,#b7b49a 0%,#8d8e78 40%,rgba(60,74,82,0) 80%)}

  .wave{position:absolute;left:0;top:0;width:556px;height:719px}

  /* footers: every line placed on its own baseline so nothing runs off the page */
  .footer{position:absolute;left:0;top:0;width:100%;height:100%;color:var(--white);pointer-events:none}
  .footer > *{position:absolute;white-space:nowrap;pointer-events:auto}
  .footer__name{font-weight:700;text-transform:uppercase}
  .footer__cta{color:var(--white);text-decoration:underline;text-underline-offset:3px}

  .page--cover .footer > *{left:0;width:556px;text-align:center}
  .page--cover .footer__name{top:614px;font-size:21px;line-height:26px;letter-spacing:.3px}
  .page--cover .footer__address{top:648px;font-size:17px;line-height:22px}
  .page--cover .footer__cta{top:680px;font-size:17px;line-height:22px}

  .page--values .footer__name{top:631px;font-size:15px;line-height:18px}
  .page--values .footer__line{top:658px;font-size:13px;line-height:18px}
  .page--values .footer__cta{top:683px;font-size:17px;line-height:22px}
  .footer--contact > *{left:20px}
  .footer--hours > *{left:308px}

  .title-band{position:absolute;left:228px;top:19px;width:328px;height:51px;background:var(--green-dark);
    clip-path:polygon(0 0,100% 0,100% 100%,0 100%,4% 50%)}
  .title-band h1{color:var(--white);font-size:19px;font-weight:700;letter-spacing:.4px;
    text-align:center;line-height:51px;padding-left:12px}

  .value{position:absolute;text-align:center;transform:translateX(-50%)}
  .value h2{font-size:10.5px;font-weight:700;color:var(--ink);text-transform:uppercase;line-height:13px;letter-spacing:.2px}
  .value__photo{width:88px;height:88px;border-radius:50%;margin:8px auto 0}
  .value p{font-size:4.6px;line-height:8px;color:var(--body);margin:0 auto}
</style>
</head>
<body>

<section class="page page--cover">
  <div class="cover-photo" role="img" aria-label="Photo of a young man in glasses looking up, with a tangle of scribbled lines rising from his head"></div>

  <div class="brand">
    <span class="brand__dot"></span>
    <span class="brand__name">Quellarive<br>Care</span>
  </div>

  <svg class="wave" viewBox="0 0 556 719" aria-hidden="true">
    <path d="M0,574 C120,540 200,545 300,572 C385,596 470,598 556,566 L556,719 L0,719 Z" fill="var(--green-dark)"/>
    <path d="M0,584 C120,550 200,555 300,582 C385,606 470,608 556,576 L556,719 L0,719 Z" fill="var(--green)"/>
  </svg>

  <div class="footer">
    <div class="footer__name">Quellarive Care</div>
    <div class="footer__address">418 Alder Bend Rd. Murfreesboro, TN 37130</div>
    <a class="footer__cta" href="#">Call Now</a>
  </div>
</section>

<section class="page page--values">
  <div class="brand">
    <span class="brand__dot"></span>
    <span class="brand__name">Quellarive<br>Care</span>
  </div>
  <div class="title-band"><h1>CORE VALUES OF CARE</h1></div>

  <article class="value" style="left:95px;top:105px;width:142px">
    <h2>An Integrative<br>Approach</h2>
    <div class="value__photo" role="img" aria-label="Photo of a red-haired woman with hands raised near her head" style="background:radial-gradient(circle at 45% 45%,#e7c3a8,#c9826a 45%,#a9a3a0 100%)"></div>
    <p style="margin-top:10px">Join us in our mission to change healthcare as we know it. Guided step-by-step by our care team, well embark on an integrative approach to cover more of the issues we face across the lifespan. Dedicated Attention People are more confused than ever when it comes to their health and they don’t know WHO or WHAT to believe. Taking charge of your health requires much more than just your typical 7-minute doctor’s visit, which can’t even cover the basics of what you need to know to heal. During your in-depth intake consultation, we take the time needed, one-on-one, to thoroughly explore the unique health concerns that keep you from living your best life.</p>
  </article>

  <article class="value" style="left:279px;top:105px;width:150px">
    <h2>Personalized<br>Care</h2>
    <div class="value__photo" role="img" aria-label="Photo of a stressed man holding his head beneath sketched notes" style="background:radial-gradient(circle at 50% 55%,#9a8c80,#bcbcbc 55%,#8e9194 100%)"></div>
    <p style="margin-top:10px">This is no “one-size-fits-all” when it comes to giving yourself the best care. Everyone is biologically unique, and as we age, we have different needs and requirements. First we get to the bottom of your worst symptoms with advanced lab evaluation. After we craft your personalized and targeted healing plan, we also empower you with the knowledge and tools to choose a smarter lifestyle that supports your healing so you don’t find yourself right back where you started a year later.</p>
  </article>

  <article class="value" style="left:455px;top:105px;width:158px">
    <h2>Innovative<br>Treatments</h2>
    <div class="value__photo" role="img" aria-label="Photo of a man in glasses with gears drawn above his head" style="background:radial-gradient(circle at 45% 55%,#b89880,#c9c4b8 50%,#e4e2dc 100%)"></div>
    <p style="margin-top:10px">Did you know that it takes on average 17 years for clinical breakthroughs to make their way into your conventional doctor’s office? That means many health care practitioners are dispensing outdated advice and not using the best evaluation techniques for your particular symptoms and circumstances. Chances are they are not even aware of the proper evaluation that could make all the difference in your healing plan. At Quellarive Care we provide the best of both worlds…traditional approaches in body &amp; mind health with clinicians who also have advanced training in functional medicine – to deliver the best, most advanced evaluation paired with current treatments and nutritional science so that we can look beyond symptoms to provide solutions to your mind and body health concerns.</p>
  </article>

  <article class="value" style="left:178px;top:346px;width:150px">
    <h2>Root<br>Cause Resolution</h2>
    <div class="value__photo" role="img" aria-label="Photo of a young woman holding her temples" style="background:radial-gradient(circle at 50% 50%,#d8b49c,#e9e3dc 55%,#f3f1ee 100%)"></div>
    <p style="margin-top:14px">We get to the bottom of WHY you feel sluggish, depressed, anxious, distracted, can’t release stubborn weight, or struggle with brain fog. Traditional outdated healthcare models focus on treating symptoms and ignore the core reason(s) behind why things you have tried aren’t working. Our practice uses the tools often found in functional medicine, including a more complete evaluation to see the factors and reasons behind why you are stuck. Many people are struggling with neurotransmitter deficiencies, nutritional deficits, stealth infections, toxicity, potential food intolerances and allergies, and gut &amp; hormonal imbalances that are not traditionally detected by conventional medical evaluation.</p>
  </article>

  <article class="value" style="left:374px;top:346px;width:158px">
    <h2>Co-Creating<br>Health</h2>
    <div class="value__photo" role="img" aria-label="Photo of a smiling woman stretching in bright white bedding" style="background:radial-gradient(circle at 55% 50%,#e2d4c4,#eef0f1 55%,#c9cdd1 100%)"></div>
    <p style="margin-top:13px">Did you know that it takes on average 17 years for clinical breakthroughs to make their way into your conventional doctor’s office? That means many health care practitioners are dispensing outdated advice and not using the best evaluation techniques for your particular symptoms and circumstances. Chances are they are not even aware of the proper evaluation that could make all the difference in your healing plan. At Quellarive Care we provide the best of both worlds…traditional approaches in body &amp; mind health with clinicians who also have advanced training in functional medicine – to deliver the best, most advanced evaluation paired with current treatments and nutritional science so that we can look beyond symptoms to provide solutions to your mind and body health concerns.</p>
  </article>

  <svg class="wave" viewBox="0 0 556 719" aria-hidden="true">
    <path d="M0,576 C50,598 90,613 150,606 C230,596 260,563 330,561 C400,560 420,593 470,591 C510,589 530,580 556,573 L556,719 L0,719 Z" fill="var(--green-dark)"/>
    <path d="M0,588 C50,610 90,625 150,618 C230,608 260,575 330,573 C400,572 420,605 470,603 C510,601 530,592 556,585 L556,719 L0,719 Z" fill="var(--green)"/>
  </svg>

  <div class="footer footer--contact">
    <div class="footer__name">Quellarive Care</div>
    <div class="footer__line">418 Alder Bend Rd. Murfreesboro, TN 37130</div>
    <a class="footer__cta" href="#">Call Now</a>
  </div>
  <div class="footer footer--hours">
    <div class="footer__name">Operating Hours</div>
    <div class="footer__line">Monday - Friday: 8AM - 7PM</div>
  </div>
</section>

</body>
</html>
```